IT company developing solutions for air cargo industry is looking for a new website

We are a professional IT company developing solutions for air cargo industry worldwide.

We are looking to update and completely redesign our current webpages: https://www.brisklane.cz/

What we like about our current pages are the animated graphics on the home page. These could stay, but not a must.

The design of the new pages should be very modern, clean, unique, creative, professional, and to make a statement. We are looking for animated graphics, cool and interesting interactions, cascading layers, etc.

Our company logo is yellow, gray and black. You don’t necessarily have to stick to this colour scheme, however the corporate colors should work well with the overal design of the web pages.
Dark mode pages are also an option.

The scope of the project would include creating a:

• Header
• Footer
• Landing page
• Navigation bar (8 tabs)
• Subpages (10)

In the first stage we are looking only for the header / footer / landing page with navigaton bar / Solutions page design.
As a second round, finalists might be asked to submit another section of the website to see their consistency in terms of the look and feel proposed for the Homepage and Solutions’ pages.
The winning designer will then complete the rest of the pages.

Attached you will find a brief for the first scope of the project. Please read the note section on slide nr. 3 carefully to understand, what we exactly are looking for to achieve.

Industry/Entity Type

Aviation

Number of Pages Required

1 page

Requirements
Must have
• See brief
Nice to have
• See brief
Should not have
• See brief

```html
<!DOCTYPE html>
<html lang="en">
<head>
<meta charset="utf-8">
<title>Brisk Lane – IT Solutions for Air Cargo</title>
<link rel="stylesheet" href="https://fonts.googleapis.com/css2?family=Roboto:wght@400;500;700&family=Cabin:wght@400;600;700&display=swap">
<style>
:root{
  --yellow:#fcc20e;
  --ink:#111111;
  --grey-dark:#3f3f3f;
  --grey-text:#444444;
  --light-bg:#f1eeee;
  --white:#ffffff;
}
*{box-sizing:border-box;margin:0;padding:0}
html,body{width:1200px;height:2294px;overflow:hidden;background:var(--white)}
body{position:relative;font-family:'Roboto',sans-serif;color:var(--ink)}

/* header */
.site-header{position:absolute;left:0;top:0;width:1200px;height:118px;background:var(--white);border-top:5px solid var(--yellow)}
.brand{position:absolute;left:113px;top:30px;display:flex;align-items:center;gap:14px;font-weight:700;font-size:46px;color:var(--grey-dark)}
.brand-square{width:30px;height:30px;background:var(--yellow)}
.tagline{position:absolute;left:663px;top:28px;font-weight:700;font-size:22px;line-height:30px;color:var(--grey-text)}

/* hero */
.hero{position:absolute;left:0;top:118px;width:1200px;height:686px;overflow:hidden}
.hero-photo{position:absolute;inset:0;background:linear-gradient(180deg,#5d6576 0%,#6f7584 35%,#4f5768 70%,#3b4253 100%)}
.main-nav{position:absolute;top:40px;left:0;width:1200px;height:22px;font-size:16px;color:var(--white)}
.main-nav span{position:absolute;top:0;white-space:nowrap;display:flex;align-items:center;gap:4px}
.hero-title{position:absolute;left:113px;top:145px;width:680px;font-family:'Cabin',sans-serif;font-weight:700;font-size:58px;line-height:73px;color:var(--white)}
.hero-text{position:absolute;left:113px;top:393px;width:650px;font-size:20px;line-height:30px;color:var(--white)}
.btn{display:flex;align-items:center;justify-content:center;background:var(--yellow);color:var(--ink);font-weight:500;font-size:16px}
.btn-learn{position:absolute;left:112px;top:547px;width:154px;height:43px}
.play{position:absolute;left:285px;top:541px}
.globe{position:absolute;left:805px;top:101px;width:258px;height:258px;border-radius:50%;background:radial-gradient(circle at 72% 42%,#ffffff 0%,#fbeee0 30%,#f6b865 62%,#ee8410 100%);box-shadow:0 4px 14px rgba(0,0,0,.25)}

/* stats */
.stats{position:absolute;left:0;top:804px;width:1200px;height:428px;background:var(--light-bg);font-family:'Cabin',sans-serif}
.stats-title{position:absolute;left:0;top:88px;width:1200px;text-align:center;font-weight:700;font-size:41px;line-height:52px}
.stat{position:absolute;top:222px;width:260px;text-align:center}
.stat-num{font-weight:600;font-size:44px;color:var(--yellow);line-height:48px;white-space:nowrap}
.stat-label{margin-top:10px;font-weight:600;font-size:20px;line-height:26px;white-space:nowrap}

/* service */
.service{position:absolute;left:0;top:1232px;width:1200px;height:689px;background:var(--white);font-family:'Cabin',sans-serif}
.service-photo{position:absolute;left:111px;top:89px;width:472px;height:514px;background:linear-gradient(180deg,#a9c4dc 0%,#cfd6dc 22%,#b9bcbf 40%,#9a9ea3 70%,#7f8287 100%)}
.service-title{position:absolute;left:663px;top:80px;width:460px;font-weight:700;font-size:43px;line-height:51px}
.service-text{position:absolute;left:663px;width:430px;font-size:16px;line-height:26px;color:var(--grey-text)}
.btn-read{position:absolute;left:664px;top:559px;width:154px;height:43px;font-family:'Roboto',sans-serif}

/* footer */
.site-footer{position:absolute;left:0;top:1921px;width:1200px;height:373px;background:var(--grey-dark);color:var(--white)}
.footer-brand{position:absolute;left:0;top:92px;width:1200px;display:flex;justify-content:center;align-items:center;gap:16px;font-weight:700;font-size:48px}
.footer-brand .brand-square{background:var(--white)}
.footer-nav{position:absolute;left:0;top:206px;width:1200px;display:flex;justify-content:center;font-size:16px}
.footer-nav span{white-space:nowrap}
.footer-nav .sep{margin:0 34px}
.contact{position:absolute;left:0;top:256px;width:1200px;display:flex;justify-content:center;gap:40px;font-size:14px}
.contact span{display:flex;align-items:center;gap:9px}
.copyright{position:absolute;left:0;top:335px;width:1200px;text-align:center;font-size:14px}
</style>
</head>
<body>

<header class="site-header">
  <div class="brand"><span>Brisk Lane</span><span class="brand-square"></span></div>
  <p class="tagline">Affordable IT Solutions That Revolutionize<br>Tomorrow‘s Air Cargo Today</p>
</header>

<section class="hero">
  <div class="hero-photo" role="img" aria-label="Cargo aircraft on the apron being loaded at dusk"></div>
  <nav class="main-nav">
    <span style="left:204px">Industries</span>
    <span style="left:310px">Solutions<svg width="9" height="6" viewBox="0 0 9 6"><polyline points="1,1 4.5,4.5 8,1" fill="none" stroke="#fff" stroke-width="1.2"/></svg></span>
    <span style="left:413px">Operational Support</span>
    <span style="left:588px">Case Studies</span>
    <span style="left:716px">Testimonials</span>
    <span style="left:842px">News</span>
    <span style="left:919px">About Us<svg width="9" height="6" viewBox="0 0 9 6"><polyline points="1,1 4.5,4.5 8,1" fill="none" stroke="#fff" stroke-width="1.2"/></svg></span>
  </nav>
  <h1 class="hero-title">Seamlessly connecting<br>the air cargo industry<br>from Manila to Tahiti</h1>
  <p class="hero-text">Blending decades of air cargo knowledge with end-to-end IT solutions. Whether you are an Airline, GSA, GHA, Forwarder or E-commerce Operator,our expertise can elevate your daily workflows, cutting down on expenses, time, and errors.</p>
  <a class="btn btn-learn">Learn More</a>
  <svg class="play" width="52" height="52" viewBox="0 0 52 52">
    <circle cx="26" cy="26" r="26" fill="#fff"/>
    <polygon points="20,15 20,37 38,26" fill="#111"/>
  </svg>
  <div class="globe" role="img" aria-label="Globe map showing a flight route from Manila to Tahiti"></div>
</section>

<section class="stats">
  <h2 class="stats-title">We are not IT tech experts attempting to do cargo!<br>We are cargo experts with programming skills!</h2>
  <div class="stat" style="left:27px"><div class="stat-num">2014</div><div class="stat-label">Established</div></div>
  <div class="stat" style="left:166px"><div class="stat-num">22</div><div class="stat-label">Employees</div></div>
  <div class="stat" style="left:370px"><div class="stat-num">11,500,000 +</div><div class="stat-label">Nr. of Annual<br>Electronic Exchanges:</div></div>
  <div class="stat" style="left:571px"><div class="stat-num">18</div><div class="stat-label">Countries<br>covered</div></div>
  <div class="stat" style="left:702px"><div class="stat-num">20+</div><div class="stat-label">Connected<br>Clients</div></div>
  <div class="stat" style="left:877px"><div class="stat-num">350,000 +</div><div class="stat-label">Nr. of<br>Annual AWBs</div></div>
</section>

<section class="service">
  <div class="service-photo" role="img" aria-label="Aerial view of a cargo jet and stacked cargo pallets on the apron"></div>
  <h2 class="service-title">Isp - Internet Service Provider</h2>
  <p class="service-text" style="top:214px">Brisk Lane Ltd. offers a stable high-speed Internet connection for demanding corporate clients in Ruzyne North cargo terminal. Service is provided continuously with an immediate solution to any malfunction. Brisk Lane provides supervision over the quality of services provided, which is carried out 24 hours a day.</p>
  <p class="service-text" style="top:392px">All network components are monitored by a network operation center running 24/7. Main supervisory instrument is a customer-oriented integrated supervision system, complemented by control and supervisory systems of technological network layers.</p>
  <a class="btn btn-read">Read More</a>
</section>

<footer class="site-footer">
  <div class="footer-brand"><span>Brisk Lane</span><span class="brand-square"></span></div>
  <nav class="footer-nav">
    <span>Industries</span><span class="sep">|</span>
    <span>Solutions</span><span class="sep">|</span>
    <span>Operational Support</span><span class="sep">|</span>
    <span>Case Studies</span><span class="sep">|</span>
    <span>Testimonials</span><span class="sep">|</span>
    <span>News</span><span class="sep">|</span>
    <span>About Us</span>
  </nav>
  <div class="contact">
    <span><svg width="13" height="13" viewBox="0 0 24 24"><path fill="#fff" d="M6.6 10.8a15 15 0 0 0 6.6 6.6l2.2-2.2a1 1 0 0 1 1-.25 11.4 11.4 0 0 0 3.6.57 1 1 0 0 1 1 1V20a1 1 0 0 1-1 1A17 17 0 0 1 3 4a1 1 0 0 1 1-1h3.5a1 1 0 0 1 1 1c0 1.25.2 2.45.57 3.57a1 1 0 0 1-.25 1z"/></svg>+420 601 234 987</span>
    <span><svg width="15" height="11" viewBox="0 0 15 11"><rect width="15" height="11" rx="1" fill="#fff"/><polyline points="0.5,0.8 7.5,6 14.5,0.8" fill="none" stroke="#3f3f3f" stroke-width="1.3"/></svg>info@brisklane.cz</span>
    <span><svg width="11" height="15" viewBox="0 0 12 16"><path fill="#fff" d="M6 0a6 6 0 0 0-6 6c0 4.5 6 10 6 10s6-5.5 6-10a6 6 0 0 0-6-6zm0 8.5A2.5 2.5 0 1 1 6 3.5a2.5 2.5 0 0 1 0 5z"/></svg>Lipová 212/4 160 00 Praha 6</span>
  </div>
  <p class="copyright">General Terms and Conditions | Copyright © 2024 Brisk Lane s.r.o.</p>
</footer>

</body>
</html>
```